New, modern business card for growing audiology practice

We need a new business card for our audiology practice. Our logo and website have recently changed (more modern) and we want our business cards to reflect this change.
We conduct hearing tests, perform earwax removals, and fit & dispense hearing aids to our patients. We are a family owned practice in which the owner is the one who works directly with the patient. I have attached logos in various formats to use, as well as two ideas I found on this website; as well as a scanned copy of our current logo. Good luck!

Industry/Entity Type

Business

Contact Information for Business Card

Company name: Tolvera Hearing Center
Provider name: Peter Wolstenby, Au.D. F/NSB
Phone number: (440) 683-5127
Address: 837 W. Lindell Ave. Marlow Falls, OH 44390
email: tolverahearing@postvane.com
website: tolverahearing.com

Colors
000000
aaaaaa
dbdbdb
cacaca
9bcb3c
afd23c
cadf82
b1b1b1

Requirements
Must have
• My card must include information in the "details" section. In the attached images, I found a few that I liked and I would like to model after - "brisky bouncin'" and "Sound Method Center".
• Must be horizontal.
• Must include logos provided. I uploaded them in various file formats and various ways.
• Must match logo font, if possible, if not, please get as close as you can.
Nice to have
• I really like the idea of having a color on one side with just the logo and company name and the contact information and provider name on the other side. I also really like the idea of having the main color dominating on the logo/company side with accent of that same color on the contact side of the card.
Should not have
• Must not be vertical.

```html
<!DOCTYPE html>
<html lang="en">
<head>
<meta charset="utf-8">
<title>Tolvera Hearing Center — Business Card</title>
<link href="https://fonts.googleapis.com/css2?family=Josefin+Sans:wght@400&family=Roboto:wght@400&family=Roboto+Condensed:ital,wght@0,700;1,700&display=swap" rel="stylesheet">
<style>
  :root {
    --stage: #3b3b3b;
    --card: #1c1c1c;
    --ink-light: #f1f1f1;
    --ink-muted: #dbdbdb;
    --brand-green: #6fb12e;
    --accent-green: #9bcb3c;
  }
  * { margin: 0; padding: 0; box-sizing: border-box; }
  html, body {
    width: 799px; height: 1200px; overflow: hidden;
    background: var(--stage);
  }
  .canvas { position: relative; width: 799px; height: 1200px; }
  .card {
    position: absolute; left: 50px; width: 700px; height: 400px;
    background: var(--card); border-radius: 6px; overflow: hidden;
  }
  .card--front { top: 90px; }
  .card--back { top: 700px; }

  /* Front */
  .wordmark {
    position: absolute; display: flex; align-items: center; gap: 14px;
    font-family: "Josefin Sans", sans-serif; font-weight: 400;
    color: var(--ink-light); text-transform: uppercase; letter-spacing: 1px;
  }
  .wordmark__dot {
    width: 26px; height: 26px; border-radius: 50%;
    background: var(--brand-green); flex: none;
  }
  .card--front .wordmark { left: 70px; top: 150px; font-size: 38px; }
  .site-line {
    position: absolute; left: 80px; top: 262px;
    font-family: "Roboto", sans-serif; font-size: 17px; letter-spacing: 5px;
    color: var(--ink-light);
  }
  .site-line__domain { color: var(--accent-green); }

  /* Back */
  .wordmark--stacked { left: 60px; top: 112px; align-items: flex-start; }
  .wordmark--stacked .wordmark__dot { margin-top: 6px; }
  .wordmark__lines { display: flex; flex-direction: column; line-height: 1; }
  .wordmark__primary { font-size: 38px; }
  .wordmark__secondary { font-size: 22px; margin-top: 6px; }
  .accent-band {
    position: absolute; left: 0; right: 0; bottom: 0; height: 14px;
    background: var(--brand-green);
  }
  .provider { position: absolute; left: 380px; top: 112px; }
  .provider__name {
    font-family: "Roboto Condensed", sans-serif; font-weight: 700; font-style: italic;
    font-size: 24px; color: var(--brand-green);
  }
  .provider__role {
    font-family: "Roboto", sans-serif; font-size: 14px; color: var(--ink-muted);
    margin-top: 4px;
  }
  .contact-list {
    position: absolute; left: 360px; top: 196px; list-style: none;
    font-family: "Roboto", sans-serif; font-size: 16px; color: var(--ink-light);
    line-height: 21px;
  }
  .contact-list li { display: flex; align-items: flex-start; gap: 10px; }
  .contact-list svg { width: 14px; height: 14px; flex: none; margin-top: 4px; fill: var(--brand-green); }
  .contact-list .spacer { width: 14px; flex: none; }
</style>
</head>
<body>
<main class="canvas">

  <section class="card card--front" aria-label="Card front">
    <div class="wordmark">
      <span class="wordmark__dot"></span>
      <span class="wordmark__text">Tolvera Hearing Center</span>
    </div>
    <p class="site-line">www.<span class="site-line__domain">tolverahearing</span>.com</p>
  </section>

  <section class="card card--back" aria-label="Card back">
    <div class="wordmark wordmark--stacked">
      <span class="wordmark__dot"></span>
      <span class="wordmark__lines">
        <span class="wordmark__primary">Tolvera</span>
        <span class="wordmark__secondary">Hearing Center</span>
      </span>
    </div>

    <div class="provider">
      <p class="provider__name">Peter Wolstenby, Au.D. F/NSB</p>
      <p class="provider__role">Owner - Audiologist</p>
    </div>

    <ul class="contact-list">
      <li>
        <svg viewBox="0 0 14 14" aria-hidden="true"><path d="M7 0a5 5 0 0 0-5 5c0 3.5 5 9 5 9s5-5.5 5-9a5 5 0 0 0-5-5zm0 7a2 2 0 1 1 0-4 2 2 0 0 1 0 4z"/></svg>
        <span>837 W. Lindell Ave.</span>
      </li>
      <li><span class="spacer"></span><span>Marlow Falls, OH 44390</span></li>
      <li>
        <svg viewBox="0 0 14 14" aria-hidden="true"><path d="M3 1l2 0 1 3-1.5 1a8 8 0 0 0 4.5 4.5l1-1.5 3 1 0 2a1.5 1.5 0 0 1-1.5 1.5A11 11 0 0 1 1.5 2.5 1.5 1.5 0 0 1 3 1z"/></svg>
        <span>(440) 683-5127</span>
      </li>
      <li>
        <svg viewBox="0 0 14 14" aria-hidden="true"><path d="M1 3h12v8H1z M1 3l6 5 6-5" fill="none" stroke="#6fb12e" stroke-width="1.5"/></svg>
        <span>tolverahearing@postvane.com</span>
      </li>
      <li>
        <svg viewBox="0 0 14 14" aria-hidden="true"><g fill="none" stroke="#6fb12e" stroke-width="1.3"><circle cx="7" cy="7" r="5.8"/><ellipse cx="7" cy="7" rx="2.5" ry="5.8"/><path d="M1.2 7h11.6"/></g></svg>
        <span>www.tolverahearing.com</span>
      </li>
    </ul>

    <div class="accent-band"></div>
  </section>

</main>
</body>
</html>
```